Car transport business

We need a new business card design. Attached is our old card sample. I would just like to adjust the logo colors (blue and red) to be brighter. I changed my name to the brighter red and the word dispatcher to a brighter blue as an example. But you can adjust those colors further. And then perhaps you can use the same colors for the card design but use your imagination.

As a suggestion so the card stands out I would like to add a clip art of car carrier truck. Attached are examples of that as well

```html
<!DOCTYPE html>
<html lang="en">
<head>
<meta charset="UTF-8">
<title>Summit Haul – Business Card</title>
<link rel="stylesheet" href="https://fonts.googleapis.com/css2?family=Montserrat:wght@500;600;800&family=Saira+Semi+Condensed:wght@700&display=swap">
<style>
  :root {
    --bg: #d9dadc;
    --card-dark: #2b2b2d;
    --card-dark-edge: #1f1f21;
    --card-light: #ffffff;
    --brand-blue: #1d74bb;
    --brand-red: #ec1c24;
    --ghost-blue: #e6eef6;
    --text-light: #ffffff;
    --text-muted: #8c8f94;
  }
  * { margin: 0; padding: 0; box-sizing: border-box; }
  html, body { width: 1200px; height: 874px; overflow: hidden; }
  body {
    background: var(--bg);
    font-family: "Montserrat", Arial, sans-serif;
    position: relative;
  }
  .card {
    position: absolute;
    left: 290px;
    width: 620px;
    height: 354px;
    border-radius: 18px;
    overflow: hidden;
    box-shadow: 0 10px 24px rgba(0,0,0,0.18);
  }
  /* Back side */
  .card--back { top: 63px; background: var(--card-dark); }
  .back-wordmark {
    position: absolute; top: 34px; left: 0; right: 0;
    text-align: center;
  }
  .wordmark-name {
    font-weight: 800; font-size: 40px; letter-spacing: 2px;
    color: var(--brand-blue); text-transform: uppercase;
    display: inline-flex; align-items: center; gap: 12px;
  }
  .wordmark-dot {
    width: 14px; height: 14px; border-radius: 50%;
    background: var(--brand-blue); display: inline-block;
  }
  .wordmark-tagline {
    display: block; margin-top: 4px;
    font-weight: 500; font-size: 11px; letter-spacing: 3px;
    color: var(--text-muted); text-transform: uppercase;
  }
  .truck-art {
    position: absolute; left: 40px; right: 40px; top: 130px; bottom: 30px;
    border-radius: 10px;
    background: linear-gradient(180deg, #333336 0%, var(--card-dark-edge) 100%);
  }
  /* Front side */
  .card--front { top: 457px; background: var(--card-light); }
  .card--front svg.swoosh { position: absolute; inset: 0; }
  .ghost-car {
    position: absolute; left: 90px; top: 30px; width: 300px; height: 200px;
    border-radius: 50% 50% 40% 40%;
    background: radial-gradient(ellipse at center, var(--ghost-blue) 0%, rgba(230,238,246,0) 70%);
  }
  .front-wordmark { position: absolute; top: 56px; left: 34px; }
  .front-wordmark .wordmark-name { font-size: 30px; gap: 10px; }
  .front-wordmark .wordmark-dot { width: 12px; height: 12px; }
  .front-wordmark .wordmark-tagline { font-size: 8.5px; letter-spacing: 2.4px; color: var(--brand-blue); }
  .contact-block {
    position: absolute; right: 34px; top: 198px;
    text-align: right; color: var(--text-light);
  }
  .person-name {
    font-family: "Saira Semi Condensed", "Arial Narrow", sans-serif;
    font-weight: 700; font-size: 26px; letter-spacing: 0.5px; line-height: 1;
    text-transform: uppercase;
  }
  .person-role { font-weight: 600; font-size: 14px; line-height: 18px; margin-top: 3px; margin-bottom: 10px; }
  .contact-list { list-style: none; }
  .contact-item {
    display: flex; justify-content: flex-end; align-items: center; gap: 8px;
    font-weight: 500; font-size: 15px; line-height: 20px;
  }
  .contact-icon { width: 13px; height: 13px; flex: none; }
</style>
</head>
<body>

  <section class="card card--back" aria-label="Card back">
    <div class="back-wordmark">
      <span class="wordmark-name"><span class="wordmark-dot"></span>Summit Haul</span>
      <span class="wordmark-tagline">The Auto Transport Professionals</span>
    </div>
    <div class="truck-art" role="img" aria-label="Dark tone-on-tone illustration of a car carrier truck"></div>
  </section>

  <section class="card card--front" aria-label="Card front">
    <div class="ghost-car" role="img" aria-label="Faint car outline decoration"></div>
    <svg class="swoosh" viewBox="0 0 620 354" width="620" height="354" aria-hidden="true">
      <path d="M110 354 C 200 240, 360 130, 620 98 L 620 106 C 370 140, 230 245, 150 354 Z" fill="var(--brand-red)"/>
      <path d="M170 354 C 250 250, 380 150, 620 110 L 620 354 Z" fill="var(--brand-blue)"/>
      <path d="M150 354 C 230 250, 370 150, 560 122 C 380 160, 250 260, 178 354 Z" fill="var(--brand-red)"/>
    </svg>

    <div class="front-wordmark">
      <span class="wordmark-name"><span class="wordmark-dot"></span>Summit Haul</span>
      <span class="wordmark-tagline">The Auto Transport Professionals</span>
    </div>

    <div class="contact-block">
      <div class="person-name">Alex Morrow</div>
      <div class="person-role">Dispatcher</div>
      <ul class="contact-list">
        <li class="contact-item">555-201-0148
          <svg class="contact-icon" viewBox="0 0 16 16"><path d="M3 1 L6 1 L7 5 L5 6.5 C6 9 7 10 9.5 11 L11 9 L15 10 L15 13 C15 14 14 15 13 15 C6 15 1 10 1 3 C1 2 2 1 3 1 Z" fill="#fff"/></svg>
        </li>
        <li class="contact-item">555-201-0172
          <svg class="contact-icon" viewBox="0 0 16 16"><rect x="4" y="1" width="8" height="14" rx="1.5" fill="none" stroke="#fff" stroke-width="1.6"/><circle cx="8" cy="12.5" r="0.9" fill="#fff"/></svg>
        </li>
        <li class="contact-item">dispatch@summithaul.com
          <svg class="contact-icon" viewBox="0 0 16 16"><rect x="1" y="3" width="14" height="10" rx="1" fill="#fff"/><path d="M1.5 3.5 L8 9 L14.5 3.5" fill="none" stroke="var(--brand-blue)" stroke-width="1.4"/></svg>
        </li>
        <li class="contact-item">www.summithaul.com
          <svg class="contact-icon" viewBox="0 0 16 16"><circle cx="8" cy="8" r="6.5" fill="none" stroke="#fff" stroke-width="1.5"/><ellipse cx="8" cy="8" rx="2.8" ry="6.5" fill="none" stroke="#fff" stroke-width="1.2"/><line x1="1.5" y1="8" x2="14.5" y2="8" stroke="#fff" stroke-width="1.2"/></svg>
        </li>
      </ul>
    </div>
  </section>

</body>
</html>
```